Business Card Update, need to bring life to the card, two sided color

We need a new business card design, are moving and changing addresses and need a new look, we have the logos already attached but need a new style moving forward. Can incorporate the color of the logo (The Green) as well, maybe a solid back? We deal with safety products revolving around static electricity and safety lighting. Would like to keep same font in second logo as well.

Target Market(s)

Electrical Safety, Lighting

Contact Information for Business Card

Dale Fenwick
Vice President
Office: 770-555-4821
Cell: 770-555-3067
dale@tkfenwick.example
www.tkfenwick.example
4700 West Harbor Boulevard
Suite #150
Roswell, GA 30076

Font styles to use
Serif
Sans Serif

Requirements
Must have
• Since 1918
Nice to have
• Could use the 100 Year Logo for back of card, would like the back of card to be the same green as logo.
Should not have
• No black cards please.

```html
<!DOCTYPE html>
<html lang="en">
<head>
<meta charset="utf-8">
<title>T.K. Fenwick Business Card</title>
<link href="https://fonts.googleapis.com/css2?family=Arimo:wght@400;700&display=swap" rel="stylesheet">
<style>
  :root {
    --brand-green: #06995a;
    --ink-green: #0a8a52;
    --paper: #ffffff;
    --backdrop: #e9ecea;
    --divider: rgba(255,255,255,.85);
    --card-radius: 24px;
  }
  * { box-sizing: border-box; margin: 0; padding: 0; }
  html, body { width: 1200px; height: 880px; overflow: hidden; }
  body {
    background: var(--backdrop);
    font-family: "Arimo", Arial, sans-serif;
    position: relative;
  }
  .card {
    position: absolute;
    width: 640px;
    height: 366px;
    border-radius: var(--card-radius);
    overflow: hidden;
    box-shadow: 0 10px 30px rgba(0,0,0,.18);
  }

  /* Back side */
  .card-back {
    left: 70px; top: 50px;
    background: var(--brand-green);
    color: var(--paper);
    text-align: center;
  }
  .card-back .mark {
    display: flex; align-items: center; justify-content: center; gap: 14px;
    margin-top: 112px;
  }
  .card-back .mark-dot {
    width: 44px; height: 44px; border-radius: 50%;
    background: var(--paper);
  }
  .card-back .mark-name { font-weight: 700; font-size: 34px; letter-spacing: .5px; }
  .card-back .since { margin-top: 10px; font-size: 15px; letter-spacing: 3px; }
  .card-back .website { margin-top: 44px; font-weight: 700; font-size: 17px; letter-spacing: .6px; }

  /* Front side */
  .card-front {
    left: 490px; top: 464px;
    background: var(--paper);
  }
  .front-identity {
    position: absolute; left: 42px; top: 50px;
    display: flex; align-items: center; gap: 18px;
    color: var(--ink-green);
  }
  .identity-dot {
    width: 96px; height: 96px; border-radius: 50%;
    border: 9px solid var(--ink-green);
  }
  .company-name { font-weight: 700; font-size: 40px; line-height: 1; }
  .company-sub { font-weight: 700; font-size: 17px; margin-top: 4px; }
  .company-since { font-size: 14px; margin-top: 5px; letter-spacing: 2px; }

  .contact-band {
    position: absolute; left: 0; right: 0; top: 204px; height: 114px;
    background: var(--brand-green);
    color: var(--paper);
    display: flex; align-items: center;
    padding: 0 22px;
  }
  .person { padding-right: 16px; border-right: 2px solid var(--divider); }
  .person-name { font-weight: 700; font-size: 22px; line-height: 1; white-space: nowrap; }
  .person-role { font-size: 14px; margin-top: 4px; text-align: right; white-space: nowrap; }
  .contact-list {
    list-style: none; padding: 0 16px; font-size: 13px; line-height: 1.6;
    border-right: 2px solid var(--divider);
  }
  .contact-list li { display: flex; align-items: center; gap: 7px; white-space: nowrap; }
  .contact-list svg { width: 13px; height: 13px; flex: none; }
  .address { padding-left: 16px; font-size: 13px; line-height: 1.6; font-style: normal; white-space: nowrap; }

  .front-website {
    position: absolute; left: 0; right: 0; bottom: 14px;
    text-align: center;
    color: var(--ink-green);
    font-weight: 700; font-size: 15px; letter-spacing: 4px;
  }
</style>
</head>
<body>

<section class="card card-back" aria-label="Business card back">
  <div class="mark">
    <span class="mark-dot"></span>
    <span class="mark-name">T.K. Fenwick</span>
  </div>
  <p class="since">SINCE 1918</p>
  <p class="website">www.tkfenwick.example</p>
</section>

<section class="card card-front" aria-label="Business card front">
  <div class="front-identity">
    <span class="identity-dot"></span>
    <div>
      <h1 class="company-name">T.K. Fenwick</h1>
      <p class="company-sub">Manufacturing Company, Inc.</p>
      <p class="company-since">SINCE 1918</p>
    </div>
  </div>

  <div class="contact-band">
    <div class="person">
      <p class="person-name">Dale Fenwick</p>
      <p class="person-role">Vice President</p>
    </div>
    <ul class="contact-list">
      <li>
        <svg viewBox="0 0 14 14" aria-hidden="true"><path d="M3 1.5l2.2 0 1 3-1.5 1a7 7 0 0 0 3.8 3.8l1-1.5 3 1 0 2.2a1.5 1.5 0 0 1-1.5 1.5A10.5 10.5 0 0 1 1.5 3 1.5 1.5 0 0 1 3 1.5z" fill="none" stroke="#fff" stroke-width="1.3"/></svg>
        Office: 770-555-4821
      </li>
      <li>
        <svg viewBox="0 0 14 14" aria-hidden="true"><rect x="3" y="1" width="8" height="12" rx="1.5" fill="none" stroke="#fff" stroke-width="1.6"/></svg>
        Cell: 770-555-3067
      </li>
      <li>
        <svg viewBox="0 0 14 14" aria-hidden="true"><rect x="1" y="3" width="12" height="8" fill="none" stroke="#fff" stroke-width="1.4"/><path d="M1 3l6 5 6-5" fill="none" stroke="#fff" stroke-width="1.4"/></svg>
        dale@tkfenwick.example
      </li>
    </ul>
    <address class="address">
      4700 West Harbor Boulevard<br>Suite #150<br>Roswell, GA 30076
    </address>
  </div>

  <p class="front-website">www.tkfenwick.example</p>
</section>

</body>
</html>
```